International Clinical Software Company needs a new business card design

We are looking for a new business card design for our company that has recently expanded into the UK market, making us a multinational company.
After having rebranded our website and produced a new style guide, we are looking for a business card that is creative and attention grabbing, while being consistent with the style and colour scheme used on the new website, www.plumvora.example
We produce care management technology for the aged care market, but the main aspect we aim to communicate is the human element of our software, and the way it assists in providing better care for aged people, and stronger relationships between aged people and the staff that care for them.
Our current business card is a dark green with gold text, which makes the text quite difficult to read, not very aesthetically appealing and the colour scheme looks quite dated.
We would like something fresh and modern, that can still be colourful but doesn't use large blocks of dark colour, and uses the colours within our logo.
Something tying in with the leaves that are used in our logo could work quite nicely, along with the Autumn/Fall colours of soft greens, yellows and reds (also in our existing logo). However also happy to look at fresh, completely out of the box ideas we may not have yet considered.
Target Market(s)
The people that receive this business card work in the aged card or health industry and are either corporate/management level staff or clinical (Registered Nurses, care workers etc.)
Industry/Entity Type
Health Product
Contact Information for Business Card
Company Name - BrindlewayCare
Company locations: United Kingdom, Australia, New Zealand
Staff Details:
Staff name: Derek Mallow
Staff job title: Executive Chairman
Staff email: d.mallow@plumvora.example
Office phone number: 01742 918576
Font styles to use
Other font styles liked:
- Calibri
Requirements
Must have
- Must include the BrindlewayCare brand name in it's current font
- Must include logo (3 leaves in gold circle)
- Must include Business Card Details
Nice to have
- Elements of gold
- White space
- Something autumn themed but not too cliched
Should not have
- No blue - used by a major competitor and we would like to differentiate from them
- Large blocks of dark green colour (the green that appears in our leaves on the logo on our current business card is the background colour and it is far too dark)

```html
<!DOCTYPE html>
<html lang="en">
<head>
<meta charset="utf-8">
<title>BrindlewayCare business card</title>
<link rel="stylesheet" href="https://fonts.googleapis.com/css2?family=Open+Sans:wght@300;400;600;700&display=swap">
<style>
  :root {
    --backdrop: #e6e6e4;
    --card-dark: #141311;
    --card-dark-soft: #1d1b17;
    --gold: #b3a478;
    --gold-light: #c9b47c;
    --white: #ffffff;
    --text-light: #f2efe8;
    --leaf-yellow: #f2c23a;
    --leaf-orange: #e8852a;
    --leaf-red: #c94a1c;
    --leaf-pale: #f4edb0;
  }
  * { box-sizing: border-box; margin: 0; padding: 0; }
  html, body {
    width: 1200px; height: 900px; overflow: hidden;
    background: var(--backdrop);
    font-family: "Open Sans", sans-serif;
  }
  .canvas {
    position: relative; width: 1200px; height: 900px;
  }
  .card {
    position: absolute; left: 250px; width: 700px; height: 400px;
    overflow: hidden; border-radius: 3px;
    box-shadow: 0 6px 18px rgba(0,0,0,0.18);
  }
  .card--front { top: 40px; background: var(--white); }
  .card--back { top: 460px; background: var(--card-dark); }

  /* Front */
  .front-artwork {
    position: absolute; left: 0; top: 0; width: 700px; height: 330px;
    background:
      radial-gradient(ellipse at 20% 20%, var(--leaf-orange) 0%, transparent 45%),
      radial-gradient(ellipse at 95% 60%, var(--leaf-red) 0%, transparent 30%),
      radial-gradient(ellipse at 75% 55%, var(--leaf-pale) 0%, transparent 50%),
      linear-gradient(110deg, var(--leaf-orange) 0%, var(--leaf-yellow) 40%, #f4dc7a 70%, #f1a040 100%);
  }
  .front-brand {
    position: absolute; right: 36px; top: 238px;
    display: flex; align-items: center; gap: 10px;
  }
  .brand-dot {
    width: 22px; height: 22px; border-radius: 50%;
    background: var(--gold);
  }
  .front-brand .brand-name {
    font-size: 26px; font-weight: 300; color: #6b5a33;
  }
  .front-band-white { position: absolute; left: 0; top: 330px; width: 700px; height: 14px; background: var(--white); }
  .front-band-gold { position: absolute; left: 0; top: 344px; width: 700px; height: 56px; background: var(--gold); }

  /* Back */
  .back-texture {
    position: absolute; left: 0; top: 0; width: 700px; height: 400px;
    background:
      radial-gradient(ellipse at 55% 30%, #2a2118 0%, transparent 45%),
      radial-gradient(ellipse at 85% 70%, #262018 0%, transparent 35%),
      radial-gradient(ellipse at 20% 80%, #231d16 0%, transparent 35%),
      var(--card-dark);
  }
  .back-brand {
    position: absolute; left: 40px; top: 86px;
    display: flex; align-items: center; gap: 14px;
  }
  .back-brand .brand-dot { width: 40px; height: 40px; }
  .back-brand .brand-name {
    font-size: 40px; font-weight: 300; color: var(--gold-light);
  }
  .person {
    position: absolute; right: 40px; top: 84px; text-align: right;
  }
  .person-name {
    font-size: 19px; font-weight: 700; letter-spacing: 0.5px;
    color: var(--gold-light); text-transform: uppercase;
  }
  .person-title {
    font-size: 18px; font-weight: 400; color: var(--text-light); margin-top: 2px;
  }
  .locations {
    position: absolute; left: 40px; top: 222px;
    display: flex; align-items: center; gap: 10px;
    font-size: 17px; color: var(--text-light);
  }
  .back-band-gold-thin { position: absolute; left: 0; top: 258px; width: 700px; height: 6px; background: var(--gold); }
  .back-band-white-thin { position: absolute; left: 0; top: 264px; width: 700px; height: 6px; background: var(--white); }
  .email {
    position: absolute; right: 40px; top: 300px;
    display: flex; align-items: center; gap: 10px;
    font-size: 17px; color: var(--text-light);
  }
  .back-band-white { position: absolute; left: 0; top: 336px; width: 700px; height: 12px; background: var(--white); }
  .back-band-gold { position: absolute; left: 0; top: 348px; width: 700px; height: 52px; background: var(--gold); }
  .icon { fill: var(--gold-light); flex: none; }
</style>
</head>
<body>
<main class="canvas">

  <section class="card card--front" aria-label="Business card front">
    <div class="front-artwork" role="img" aria-label="Photograph of golden and orange autumn maple leaves against a soft blurred background"></div>
    <div class="front-brand">
      <span class="brand-dot"></span>
      <span class="brand-name">BrindlewayCare</span>
    </div>
    <div class="front-band-white"></div>
    <div class="front-band-gold"></div>
  </section>

  <section class="card card--back" aria-label="Business card back">
    <div class="back-texture" role="img" aria-label="Faint dark autumn leaf silhouettes over a near-black background"></div>

    <div class="back-brand">
      <span class="brand-dot"></span>
      <span class="brand-name">BrindlewayCare</span>
    </div>

    <div class="person">
      <p class="person-name">Derek Mallow</p>
      <p class="person-title">Executive Chairman</p>
    </div>

    <p class="locations">
      <svg class="icon" width="12" height="16" viewBox="0 0 12 16" aria-hidden="true">
        <path d="M6 0C2.7 0 0 2.6 0 5.9 0 10.3 6 16 6 16s6-5.7 6-10.1C12 2.6 9.3 0 6 0zm0 8.2A2.3 2.3 0 1 1 6 3.6a2.3 2.3 0 0 1 0 4.6z"/>
      </svg>
      United Kingdom, Australia, New Zealand
    </p>

    <div class="back-band-gold-thin"></div>
    <div class="back-band-white-thin"></div>

    <p class="email">
      <svg class="icon" width="16" height="12" viewBox="0 0 16 12" aria-hidden="true">
        <path d="M0 0h16v12H0z" fill="none"/>
        <path d="M0 1.2 8 6.5l8-5.3V12H0z"/>
        <path d="M0 0h16L8 5.2z"/>
      </svg>
      d.mallow@plumvora.example
    </p>

    <div class="back-band-white"></div>
    <div class="back-band-gold"></div>
  </section>

</main>
</body>
</html>
```